Website for Dental Office - The Bright Arch Clinic

The bright arch clinic is a dental office offering cosmetic dentistry, general dentistry, and multi-specialty dental care all under one roof in our state-of-the-art cosmetic dental center. We are particularly striving to provide services that fit the need of the young generation. Thus, we hope to have a modern, professional concise website that represents our spirit.

*Should be able to switch from English to Chinese

6 sections besides homepage:
Home, Meet us, Services,
Patient Info, Cases&Reviews, Blog, Contact

The Services sections should contain multiple subsections such as cleaning and prevention, cosmetic dentistry, implant dentistry, removable dentures, etc...
The Patient Info section is also intended to contain several subsections such as
New Patient offer, accepted Insurance, patient portal, helpful tips, etc...

Target Market(s)

young generation

Coding

Coded - Design and coding required

Number of Pages Required

5+ page

Font styles to use
Sans Serif

Colors
0592cd
33a6d7
85cae6
00a990
33b8a4
86cfc6
cee9f5
cfeae6
3277b5

Requirements
Must have
• *Should be able to switch from English to Chinese
Nice to have
• http://www.thebrightarchclinic.com/
• As a reference, the above link is the current website, but we would like to change the appearance and the content (our new logo's picture is attached)

```html
<!DOCTYPE html>
<html lang="en">
<head>
<meta charset="utf-8">
<title>Blog — The Bright Arch Clinic</title>
<link href="https://fonts.googleapis.com/css2?family=Montserrat:wght@400;600;700;800&family=Open+Sans:wght@400;600;700&display=swap" rel="stylesheet">
<style>
:root{
  --blue:#0592cd;
  --blue-mid:#33a6d7;
  --blue-soft:#85cae6;
  --blue-pale:#cee9f5;
  --blue-deep:#3277b5;
  --teal:#00a990;
  --teal-mid:#33b8a4;
  --teal-soft:#86cfc6;
  --teal-pale:#cfeae6;
  --ink:#333b42;
  --muted:#7d868e;
  --line:#e4e8eb;
  --hero-bg:#f1f6f9;
  --footer-bg:#f7f9fa;
  --bar-bg:#eceff1;
  --white:#ffffff;
}
*{box-sizing:border-box;margin:0;padding:0}
html,body{width:855px;height:1200px;overflow:hidden}
body{font-family:"Open Sans",Arial,sans-serif;color:var(--ink);background:var(--white);position:relative}

/* header */
.site-header{height:56px;display:flex;align-items:center;padding:0 34px 0 38px;background:var(--white);border-bottom:1px solid var(--line)}
.brand{display:flex;align-items:center;gap:8px;font-family:"Montserrat",sans-serif;font-weight:700;color:var(--blue);font-size:14px;line-height:1.05;text-transform:uppercase}
.brand-mark{width:26px;height:26px;background:var(--blue);border-radius:3px;flex:none}
.main-nav{display:flex;gap:15px;margin-left:auto;font-family:"Montserrat",sans-serif;font-size:8.5px;font-weight:600;letter-spacing:.3px;text-transform:uppercase}
.main-nav a{color:var(--ink);text-decoration:none}
.main-nav a.active{color:var(--blue)}
.phone-badge{margin-left:16px;width:44px;height:44px;border-radius:50%;background:var(--blue);color:var(--white);font-size:7px;font-weight:700;display:flex;align-items:center;justify-content:center;text-align:center}
.lang-btn{margin-left:8px;background:var(--teal);color:var(--white);font-size:8px;font-weight:700;padding:6px 9px;border-radius:3px;font-family:"Montserrat",sans-serif}

/* hero */
.page-hero{height:190px;background:var(--hero-bg);text-align:center;padding-top:52px}
.page-hero h1{font-family:"Montserrat",sans-serif;font-weight:800;font-size:40px;letter-spacing:1px;color:var(--blue)}
.page-hero p{width:380px;margin:14px auto 0;font-size:9px;line-height:1.6;color:var(--muted)}

/* blog grid */
.blog-grid{display:grid;grid-template-columns:repeat(3,200px);column-gap:13px;row-gap:24px;justify-content:center;margin-top:6px}
.post-card{background:var(--white);height:266px}
.post-media{height:124px;display:block}
.post-body{padding:12px 0 0}
.post-title{font-family:"Montserrat",sans-serif;font-size:9.5px;font-weight:700;line-height:1.45;color:var(--ink)}
.post-date{font-size:7.5px;color:var(--muted);margin:5px 0 7px}
.post-excerpt{font-size:8px;line-height:1.6;color:var(--muted)}
.read-more{display:inline-block;margin-top:9px;font-family:"Montserrat",sans-serif;font-size:7.5px;font-weight:700;color:var(--teal);text-transform:uppercase;letter-spacing:.4px}

.m1{background:linear-gradient(135deg,#6b4a3a,#c99b82 55%,#efe0d6)}
.m2{background:linear-gradient(135deg,#e9f3f8,#b9d6e4 60%,#d8a98c)}
.m3{background:linear-gradient(135deg,#dfe5e9,#9aa7b0 60%,#5d6b75)}
.m4{background:linear-gradient(135deg,#2d6e64,#7fb6ac 55%,#e2c3a2)}
.m5{background:linear-gradient(135deg,#f7c7c6,#f3aeb0 60%,#fbe1dd)}
.m6{background:linear-gradient(135deg,#f4f6f5,#b8d8cf 55%,#3f8f7d)}

/* banner */
.cta-band{position:absolute;left:0;top:890px;width:855px;height:96px}
.cta-band svg{position:absolute;inset:0}
.cta-copy{position:absolute;left:112px;top:24px;color:var(--white)}
.cta-copy small{display:block;font-size:7.5px;opacity:.9;margin-bottom:4px}
.cta-copy h2{font-family:"Montserrat",sans-serif;font-weight:800;font-size:27px;letter-spacing:.5px;white-space:nowrap}
.cta-button{position:absolute;left:566px;top:35px;background:var(--white);color:var(--blue-deep);font-family:"Montserrat",sans-serif;font-weight:700;font-size:8.5px;letter-spacing:.4px;padding:9px 18px;border-radius:18px;text-transform:uppercase}

/* footer */
.site-footer{position:absolute;left:0;top:986px;width:855px;height:170px;background:var(--footer-bg);display:flex;padding:22px 0 0 112px}
.footer-brand{width:150px}
.footer-brand .brand{font-size:12px}
.social{display:flex;gap:6px;margin-top:14px}
.social span{width:20px;height:20px;border-radius:50%;background:var(--blue-mid)}
.footer-col{font-size:7.5px;line-height:1.75;color:var(--muted)}
.footer-col h3{font-family:"Montserrat",sans-serif;font-size:8.5px;font-weight:700;color:var(--ink);text-transform:uppercase;margin-bottom:6px}
.links{width:140px}
.hours{width:200px}
.hours .row{display:flex;justify-content:space-between;width:150px}
.contact .item{display:flex;align-items:center;gap:6px}
.contact svg{width:9px;height:9px;flex:none}

.bottom-bar{position:absolute;left:0;top:1156px;width:855px;height:44px;background:var(--bar-bg);display:flex;align-items:center;justify-content:space-between;padding:0 112px;font-size:7.5px;color:var(--muted)}
.bottom-bar b{color:var(--blue);font-weight:600}
</style>
</head>
<body>

<header class="site-header">
  <div class="brand"><span class="brand-mark"></span><span>The Bright Arch<br>Clinic</span></div>
  <nav class="main-nav">
    <a href="#">Home</a><a href="#">About Us</a><a href="#">Services</a><a href="#">Patient Info</a><a href="#">Reviews</a><a class="active" href="#">Blog</a><a href="#">Contact</a>
  </nav>
  <div class="phone-badge">555.014<br>.2286</div>
  <div class="lang-btn">中文</div>
</header>

<section class="page-hero">
  <h1>BLOG</h1>
  <p>Helpful notes from our team on brushing, whitening, implants and caring for your smile at every stage of life, written for busy modern patients.</p>
</section>

<main class="blog-grid">
  <article class="post-card">
    <div class="post-media m1" role="img" aria-label="Smiling woman with bright teeth"></div>
    <div class="post-body">
      <h2 class="post-title">Five simple daily habits that keep your teeth bright and healthy.</h2>
      <div class="post-date">7 September 2017</div>
      <p class="post-excerpt">Small changes to your routine can protect enamel, freshen breath and keep gums strong between your regular cleanings.</p>
      <span class="read-more">Read More</span>
    </div>
  </article>
  <article class="post-card">
    <div class="post-media m2" role="img" aria-label="Dentist showing a patient her smile in a mirror"></div>
    <div class="post-body">
      <h2 class="post-title">What to expect at your very first visit to our new clinic.</h2>
      <div class="post-date">7 September 2017</div>
      <p class="post-excerpt">From check-in to your exam, here is a friendly walk through everything that happens on your first day with us.</p>
      <span class="read-more">Read More</span>
    </div>
  </article>
  <article class="post-card">
    <div class="post-media m3" role="img" aria-label="Modern dental treatment chair"></div>
    <div class="post-body">
      <h2 class="post-title">Inside our treatment rooms and the tools we use every day.</h2>
      <div class="post-date">7 September 2017</div>
      <p class="post-excerpt">Take a quick tour of the equipment that makes modern care faster, gentler and more comfortable for every patient.</p>
      <span class="read-more">Read More</span>
    </div>
  </article>
  <article class="post-card">
    <div class="post-media m4" role="img" aria-label="Laughing child wearing a winter hood"></div>
    <div class="post-body">
      <h2 class="post-title">Helping kids build happy habits for a lifetime of good smiles.</h2>
      <div class="post-date">7 September 2017</div>
      <p class="post-excerpt">Tips for parents on brushing games, healthy snacks and making the dentist a place children look forward to.</p>
      <span class="read-more">Read More</span>
    </div>
  </article>
  <article class="post-card">
    <div class="post-media m5" role="img" aria-label="Hands holding a toothbrush on a pink background"></div>
    <div class="post-body">
      <h2 class="post-title">Choosing the right toothbrush and paste for your own needs.</h2>
      <div class="post-date">7 September 2017</div>
      <p class="post-excerpt">Soft or medium, manual or electric, whitening or sensitive? Our hygienists explain what really makes the difference.</p>
      <span class="read-more">Read More</span>
    </div>
  </article>
  <article class="post-card">
    <div class="post-media m6" role="img" aria-label="Dental hygienist at work in a bright clinic"></div>
    <div class="post-body">
      <h2 class="post-title">Why a professional cleaning twice a year really matters.</h2>
      <div class="post-date">7 September 2017</div>
      <p class="post-excerpt">Regular cleanings remove buildup brushing misses and help us spot small problems long before they grow.</p>
      <span class="read-more">Read More</span>
    </div>
  </article>
</main>

<section class="cta-band">
  <svg width="855" height="96" viewBox="0 0 855 96" aria-hidden="true">
    <defs>
      <linearGradient id="bandFill" x1="0" y1="0" x2="1" y2="0">
        <stop offset="0" stop-color="#0592cd"/>
        <stop offset="1" stop-color="#00a990"/>
      </linearGradient>
    </defs>
    <rect width="855" height="96" fill="#33b8a4"/>
    <polygon points="0,0 560,0 520,96 0,96" fill="url(#bandFill)"/>
  </svg>
  <div class="cta-copy">
    <small>Gentle, modern care for every member of your family.</small>
    <h2>YOUR SMILE. OUR PASSION.</h2>
  </div>
  <div class="cta-button">Book an Appointment</div>
</section>

<footer class="site-footer">
  <div class="footer-brand">
    <div class="brand"><span class="brand-mark"></span><span>The Bright Arch<br>Clinic</span></div>
    <div class="social"><span></span><span></span><span></span></div>
  </div>
  <div class="footer-col links">
    <h3>Useful Links</h3>
    <div>Home</div><div>About Us</div><div>Services</div><div>Patient Info</div><div>Cases &amp; Reviews</div><div>Blog</div><div>Contact</div>
  </div>
  <div class="footer-col hours">
    <h3>Opening Hours</h3>
    <div class="row"><span>Sunday &amp; Holidays</span><span>Closed</span></div>
    <div class="row"><span>Monday</span><span>9:00am – 6:00pm</span></div>
    <div class="row"><span>Tuesday</span><span>9:00am – 6:00pm</span></div>
    <div class="row"><span>Wednesday</span><span>9:00am – 6:00pm</span></div>
    <div class="row"><span>Thursday</span><span>9:00am – 6:00pm</span></div>
    <div class="row"><span>Friday</span><span>9:00am – 5:00pm</span></div>
    <div class="row"><span>Saturday</span><span>9:00am – 1:00pm</span></div>
  </div>
  <div class="footer-col contact">
    <h3>Contact Info</h3>
    <div class="item"><svg viewBox="0 0 10 10"><path d="M5 0a3.5 3.5 0 0 0-3.5 3.5C1.5 6 5 10 5 10s3.5-4 3.5-6.5A3.5 3.5 0 0 0 5 0zm0 5a1.5 1.5 0 1 1 0-3 1.5 1.5 0 0 1 0 3z" fill="#33a6d7"/></svg><span>48 Harbor Lane, Suite 210</span></div>
    <div class="item"><svg viewBox="0 0 10 10"></svg><span>Larkfield, ST 10990</span></div>
    <div class="item"><svg viewBox="0 0 10 10"><path d="M2 0.5l2 2-1 1.2a6 6 0 0 0 3.3 3.3l1.2-1 2 2L8.3 9.5C4.5 9.5.5 5.5.5 1.7z" fill="#33a6d7"/></svg><span>555.014.2286</span></div>
    <div class="item"><svg viewBox="0 0 10 10"><rect x=".5" y="2" width="9" height="6" fill="none" stroke="#33a6d7"/><path d="M.5 2L5 5.5 9.5 2" fill="none" stroke="#33a6d7"/></svg><span>hello@brightarchclinic.com</span></div>
  </div>
</footer>

<div class="bottom-bar">
  <span><b>The Bright Arch Clinic</b> · 2017 All Rights Reserved</span>
  <span>Privacy Policy and Terms of Use</span>
</div>

</body>
</html>
```